Local Roofing/Construction company business needs new biz card design

We need a new business card design, current cards are from the start of this operation and generic at best. We are a local Construction Company (General Contractor) with a majority of our work originating from insurance claims-exterior finish work is the main focus (Roofs-Siding-Gutters etc). Heavily involved with homeowners and the low ball offers they receive from insurance company's after a insurable event takes place. I have attached some of our original logo file(s) below.

```html
<!DOCTYPE html>
<html lang="en">
<head>
<meta charset="utf-8">
<title>Ridgeline Builders – Business Card</title>
<link rel="stylesheet" href="https://fonts.googleapis.com/css2?family=Open+Sans:wght@400;700&display=swap">
<style>
  :root {
    --backdrop: #232323;
    --card-dark: #061c22;
    --plate-dark: #0b2329;
    --plate-edge: #33464b;
    --plate-text: #7c8b8f;
    --brand-green: #4cbb6c;
    --green-deep: #2fa654;
    --green-light: #8fdaa3;
    --text-light: #e8eeee;
    --text-white: #ffffff;
  }
  * { margin: 0; padding: 0; box-sizing: border-box; }
  html, body {
    width: 1200px; height: 780px; overflow: hidden;
    background: var(--backdrop);
    font-family: "Open Sans", Arial, sans-serif;
  }
  .canvas {
    position: relative; width: 1200px; height: 780px;
    display: flex; align-items: center; justify-content: center; gap: 40px;
  }
  .card {
    position: relative; width: 540px; height: 310px;
    border-radius: 4px; overflow: hidden;
    box-shadow: 0 18px 40px rgba(0,0,0,.55);
  }

  /* Front */
  .card-front { background: var(--card-dark); }
  .brand-plate {
    position: absolute; left: 26px; top: 24px; bottom: 24px; width: 92px;
    background: var(--plate-dark);
    border: 2px solid var(--plate-edge);
    border-radius: 10px;
    display: flex; align-items: center; justify-content: center;
    overflow: hidden;
  }
  .brand-plate .brand-name {
    writing-mode: vertical-rl;
    transform: rotate(180deg);
    white-space: nowrap;
    font-weight: 700; font-size: 19px; letter-spacing: 1px; line-height: 1;
    color: var(--plate-text);
  }
  .contact {
    position: absolute; right: 44px; top: 50px;
    text-align: right; color: var(--text-light);
  }
  .person-name { font-weight: 700; font-size: 30px; line-height: 1.1; }
  .person-name .first { color: var(--brand-green); }
  .person-name .last { color: var(--text-white); }
  .person-title { font-size: 15px; margin-top: 2px; }
  .address { font-size: 14px; margin-top: 10px; line-height: 1.35; }
  .contact-list { list-style: none; margin-top: 12px; font-size: 14px; line-height: 1.6; }
  .contact-list li { display: flex; justify-content: flex-end; align-items: center; gap: 8px; }
  .contact-list svg { width: 13px; height: 13px; fill: var(--brand-green); flex: none; }
  .name-tab {
    position: absolute; right: 0; top: 50px; width: 18px; height: 34px;
    background: var(--brand-green);
  }

  /* Back */
  .card-back { background: var(--brand-green); }
  .back-pattern {
    position: absolute; inset: 0;
    background: linear-gradient(120deg, var(--green-deep) 0%, var(--brand-green) 55%, var(--green-light) 100%);
  }
  .back-badge {
    position: absolute; right: 46px; bottom: 40px;
    background: var(--card-dark); border-radius: 8px;
    padding: 8px 16px; display: flex; align-items: center; gap: 8px;
  }
  .back-badge .mark { width: 12px; height: 12px; background: var(--brand-green); }
  .back-badge .brand-name { color: var(--text-white); font-weight: 700; font-size: 17px; letter-spacing: .5px; }
</style>
</head>
<body>
<main class="canvas">
  <section class="card card-front" aria-label="Card front">
    <div class="brand-plate"><span class="brand-name">RIDGELINE BUILDERS</span></div>
    <div class="name-tab"></div>
    <div class="contact">
      <h1 class="person-name"><span class="first">Marta</span> <span class="last">Hollis</span></h1>
      <p class="person-title">Managing Director</p>
      <p class="address">42 Cedar Hollow<br>Dr, Lakeport, MO 63012</p>
      <ul class="contact-list">
        <li>555-210-4480
          <svg viewBox="0 0 24 24"><path d="M6.6 10.8a15 15 0 0 0 6.6 6.6l2.2-2.2a1 1 0 0 1 1-.25 11.4 11.4 0 0 0 3.6.6 1 1 0 0 1 1 1V20a1 1 0 0 1-1 1A17 17 0 0 1 3 4a1 1 0 0 1 1-1h3.5a1 1 0 0 1 1 1c0 1.250.2 2.450.6 3.6a1 1 0 0 1-.25 1z"/></svg></li>
        <li>555-210-4499 (Emergency)
          <svg viewBox="0 0 24 24"><path d="M6.6 10.8a15 15 0 0 0 6.6 6.6l2.2-2.2a1 1 0 0 1 1-.25 11.4 11.4 0 0 0 3.6.6 1 1 0 0 1 1 1V20a1 1 0 0 1-1 1A17 17 0 0 1 3 4a1 1 0 0 1 1-1h3.5a1 1 0 0 1 1 1c0 1.250.2 2.450.6 3.6a1 1 0 0 1-.25 1z"/></svg></li>
        <li>www.ridgelinebuilders.com
          <svg viewBox="0 0 24 24"><path d="M12 2a10 10 0 1 0 0 20 10 10 0 0 0 0-20zm6.9 6h-3a15 15 0 0 0-1.3-3.6A8 8 0 0 1 18.9 8zM12 4c.8 1.2 1.5 2.5 1.9 4h-3.8c.4-1.5 1.1-2.8 1.9-4zM4.3 14a8 8 0 0 1 0-4h3.4a16 16 0 0 0 0 4zm.8 2h3a15 15 0 0 0 1.3 3.6A8 8 0 0 1 5.1 16zm3-8h-3a8 8 0 0 1 4.3-3.6A15 15 0 0 0 8.1 8zM12 20c-.8-1.2-1.5-2.5-1.9-4h3.8c-.4 1.5-1.1 2.8-1.9 4zm2.3-6H9.7a14 14 0 0 1 0-4h4.6a14 14 0 0 1 0 4zm.3 5.6a15 15 0 0 0 1.3-3.6h3a8 8 0 0 1-4.3 3.6zm1.7-5.6a16 16 0 0 0 0-4h3.4a8 8 0 0 1 0 4z"/></svg></li>
        <li>hello@ridgelinebuilders.com
          <svg viewBox="0 0 24 24"><path d="M2 5h20v14H2zm2 2v.5l8 5 8-5V7zm0 2.8V17h16V9.8l-8 5z"/></svg></li>
      </ul>
    </div>
  </section>

  <section class="card card-back" aria-label="Card back">
    <div class="back-pattern" role="img" aria-label="Repeating brand monogram pattern fading from green to light green"></div>
    <div class="back-badge"><span class="mark"></span><span class="brand-name">RIDGELINE BUILDERS</span></div>
  </section>
</main>
</body>
</html>
```